Catalogue Design Project

We need a catalog design for a new private university called Redwell Institute Bayshore (see website www.rwi-bs.org). The catalog should be about 30 pages maximum and will include items such as General Information, Academic schedule, department descriptions, program descriptions, course descriptions, school policies, student services, admissions, San diego Lifestyle, etc.
I will provide the text but I need a professional design with regard to page layouts. I have provided some examples.
Ok, i posted the catalog content, just missing course descriptions.
Target Market(s)
Young Professionals, Foreign Students
Industry/Entity Type
University
Look and feel
Each slider illustrates characteristics of the customer's brand and the style your logo design should communicate.

```html
<!DOCTYPE html>
<html lang="en">
<head>
<meta charset="utf-8">
<title>Academic Programs – Import/Export Business Certificate</title>
<link rel="stylesheet" href="https://fonts.googleapis.com/css2?family=Carlito:wght@400;700&display=swap">
<style>
  :root {
    --ink: #1c1c1c;
    --brand-blue: #2e5d93;
    --brand-blue-dark: #23456f;
    --rule-blue: #8fa9c9;
    --mark-grey: #a9adb3;
    --footer-grey: #8a8d91;
    --paper: #ffffff;
    --book-light: #f4eee2;
    --book-warm: #d9c6a3;
  }
  html, body {
    margin: 0;
    padding: 0;
    width: 927px;
    height: 1200px;
    overflow: hidden;
    background: var(--paper);
  }
  .page {
    position: relative;
    width: 927px;
    height: 1200px;
    overflow: hidden;
    background: var(--paper);
    font-family: "Carlito", "Calibri", Arial, sans-serif;
    color: var(--ink);
  }
  .header-image {
    position: absolute;
    left: 540px;
    top: 0;
    width: 387px;
    height: 150px;
    background: linear-gradient(90deg, rgba(255,255,255,1) 0%, var(--book-light) 35%, var(--book-warm) 100%);
  }
  .brand-mark {
    position: absolute;
    left: 60px;
    top: 58px;
    width: 152px;
    height: 30px;
    border-radius: 15px;
    background: linear-gradient(90deg, var(--brand-blue) 0%, var(--mark-grey) 45%, var(--mark-grey) 75%, var(--brand-blue) 100%);
    opacity: .85;
  }
  .section-title {
    position: absolute;
    left: 303px;
    width: 321px;
    top: 92px;
    margin: 0;
    text-align: center;
    font-weight: 400;
    font-size: 31px;
    letter-spacing: .3px;
    color: var(--ink);
  }
  .title-bar {
    position: absolute;
    left: 303px;
    top: 132px;
    width: 321px;
    height: 17px;
    background: var(--brand-blue);
  }
  .title-rule {
    position: absolute;
    left: 0;
    top: 149px;
    width: 927px;
    height: 2px;
    background: var(--rule-blue);
  }
  .category-tab {
    position: absolute;
    left: 0;
    top: 177px;
    width: 410px;
    height: 42px;
    padding-left: 24px;
    box-sizing: border-box;
    border-radius: 0 14px 14px 0;
    background: linear-gradient(180deg, #4a76ab 0%, var(--brand-blue) 45%, var(--brand-blue-dark) 100%);
    box-shadow: 2px 2px 0 #1a3558;
    color: #fff;
    font-size: 30px;
    line-height: 42px;
    letter-spacing: .3px;
    margin: 0;
    font-weight: 400;
  }
  .program {
    position: absolute;
    left: 80px;
    top: 244px;
    width: 805px;
  }
  .program-title {
    margin: 0 0 8px;
    text-align: center;
    font-size: 25px;
    font-weight: 700;
  }
  .program p {
    margin: 0;
    font-size: 19px;
    line-height: 36.4px;
    text-align: justify;
  }
  .program .gap { margin-top: 36.4px; }
  .label-underline { text-decoration: underline; }
  .footer-rule {
    position: absolute;
    left: 0;
    top: 1156px;
    width: 927px;
    height: 1px;
    background: var(--rule-blue);
  }
  .footer-text {
    position: absolute;
    right: 38px;
    top: 1170px;
    margin: 0;
    font-size: 12px;
    letter-spacing: .5px;
    color: var(--footer-grey);
  }
</style>
</head>
<body>
<div class="page">
  <div class="header-image" role="img" aria-label="Open book with aged pages"></div>
  <div class="brand-mark" role="img" aria-label="Redwell Institute Bayshore brand mark"></div>

  <h1 class="section-title">ACADEMIC PROGRAMS</h1>
  <div class="title-bar"></div>
  <div class="title-rule"></div>

  <h2 class="category-tab">CERTIFICATE PROGRAMS</h2>

  <section class="program">
    <h3 class="program-title">Import/Export Business Certificate</h3>
    <p>This course covers the exploration process of pursuing a business opportunity involving the purchase or selling of goods or even launching a career in the field of import/export. Students of the certificate program will learn to focus their energy on finding buyers, understanding what their interests are and negotiating a profitable way to meet their needs.</p>
    <p class="gap">The certificate class will also include in-depth discussions of such topics as the functions of traffic management services performed by freight forwarders as utilized in shipping bulk products across multiple check points, the ever-changing of governmental restrictions and regulations, efficient port and trade routes, and completion of required documentation for the facilitation and coordination of moving goods domestically and internationally.</p>
    <p><strong>Hours:</strong> 6 hours per week</p>
    <p><strong>Length:</strong> 8 weeks per course</p>
    <p class="gap"><span class="label-underline">Course:</span></p>
    <p>BUS 602 Fundamentals of Importing &amp; Exporting</p>
    <p class="gap"><span class="label-underline">Learning Outcome:</span></p>
    <p>Acquire in-depth knowledge of international markets, methods to locate buyers and sellers, and learn how to price, position, and sell a product or service to the right customer.</p>
  </section>

  <div class="footer-rule"></div>
  <p class="footer-text">12::: REDWELL INSTITUTE</p>
</div>
</body>
</html>
```